Martin R Cole DDS (dentist) needs a business card/business logo design

I would like an eye-catchingly conservative or elegant graphic presentation of my business name with the elements: prevention, restoration, and cosmetics (these are the services I'd like to emphasize) .
The business card would have room for address lines, phone and fax, web address. No standard teeth or oral representations please. Should communicate professionalism. Whatever color scheme works.

Thank you

Target Market(s)

I just want a good looking business card

Industry/Entity Type

Conservative

Contact Information for Business Card

Adress: 4163 Brisdale Ave Lakewood CA 90648 Phone: 562 419 3086 FAX 562 419 5274 Web: Fernhilldental.com

Font styles to use
Sans Serif

Colors
0255a3

Requirements
Must have
• business name with the elements: prevention, restoration, and cosmetics (these are the services I'd like to emphasize)
• communicates professionalism
Nice to have
• eye catching but not flashy graphics
Should not have
• no pictures of teeth or dental instruments

```html
<!DOCTYPE html>
<html lang="en">
<head>
<meta charset="utf-8">
<title>Martin R Cole DDS – Business Card</title>
<link rel="stylesheet" href="https://fonts.googleapis.com/css2?family=Ubuntu:wght@400;500;700&display=swap">
<style>
  :root {
    --slate: #4f6468;
    --ink: #4a5e62;
    --paper: #ffffff;
    --backdrop: #e7e9ea;
  }
  * { margin: 0; padding: 0; box-sizing: border-box; }
  html, body {
    width: 1200px; height: 1000px; overflow: hidden;
    background: var(--backdrop);
    font-family: "Ubuntu", sans-serif;
  }
  .card {
    position: absolute; left: 100px; top: 210px;
    width: 1000px; height: 580px;
    background: var(--paper);
    box-shadow: 0 8px 30px rgba(0,0,0,.18);
    overflow: hidden;
  }
  .card__bands { position: absolute; inset: 0; }
  .identity {
    position: absolute; left: 60px; top: 138px; width: 420px;
    text-align: center; color: var(--ink);
  }
  .identity__name { font-weight: 700; font-size: 32px; letter-spacing: .2px; }
  .identity__role { font-weight: 400; font-size: 22px; margin-top: 2px; padding-left: 80px; }
  .contact { position: absolute; left: 36px; color: var(--ink); font-size: 22px;
    display: flex; align-items: center; gap: 8px; letter-spacing: .5px; }
  .contact svg { width: 26px; height: 26px; fill: var(--ink); flex: none; }
  .contact--phone { top: 297px; }
  .contact--fax { top: 357px; }
  .contact--web { top: 417px; }
  .contact--address { top: 477px; }
  .tagline {
    position: absolute; right: 40px; top: 58px;
    font-weight: 500; font-size: 24px; color: var(--ink);
  }
  .brand {
    position: absolute; right: 42px; bottom: 52px;
    display: flex; align-items: center; gap: 12px;
    font-weight: 700; font-size: 30px; color: var(--slate);
  }
  .brand__mark { width: 22px; height: 22px; background: var(--slate); }
</style>
</head>
<body>
<div class="card">
  <svg class="card__bands" viewBox="0 0 1000 580" width="1000" height="580" aria-hidden="true">
    <g fill="var(--slate)">
      <polygon points="0,0 500,0 512,120 0,120"/>
      <polygon points="0,232 523,232 529,290 0,290"/>
      <polygon points="0,336 533,336 535,350 0,350"/>
      <polygon points="0,396 539,396 540,410 0,410"/>
      <polygon points="0,456 545,456 546,470 0,470"/>
      <polygon points="0,516 551,516 558,580 0,580"/>
    </g>
  </svg>

  <div class="identity">
    <div class="identity__name">Martin R Cole DDS</div>
    <div class="identity__role">Dentist</div>
  </div>

  <div class="contact contact--phone">
    <svg viewBox="0 0 24 24"><path d="M3 8c0-2 4-4 9-4s9 2 9 4v2h-4V8c-1-.6-3-1-5-1s-4 .4-5 1v2H3z"/><path d="M6 11l2-3h8l2 3v8H6z"/></svg>
    <span>: 562- 419- 3086</span>
  </div>
  <div class="contact contact--fax">
    <svg viewBox="0 0 24 24"><path d="M7 3h10v5H7z"/><path d="M3 9h18v9h-3v-4H6v4H3z"/><path d="M7 15h10v6H7z"/></svg>
    <span>: 562- 419- 5274</span>
  </div>
  <div class="contact contact--web">
    <svg viewBox="0 0 24 24"><circle cx="12" cy="12" r="10"/><rect x="2" y="10" width="20" height="4" fill="#fff"/></svg>
    <span>: www.Fernhilldental.com</span>
  </div>
  <div class="contact contact--address">
    <svg viewBox="0 0 24 24"><path d="M12 2a6 6 0 0 1 6 6c0 4-6 10-6 10S6 12 6 8a6 6 0 0 1 6-6zm0 4a2 2 0 1 0 0 4 2 2 0 0 0 0-4z"/><path d="M3 18h5v2H5v1h14v-3h2v5H3z"/></svg>
    <span>: 4163 Brisdale Ave, Lakewood, CA 90648</span>
  </div>

  <div class="tagline">Prevention, Restoration and Cosmetics</div>

  <div class="brand">
    <span class="brand__mark"></span>
    <span class="brand__name">Martin R Cole DDS</span>
  </div>
</div>
</body>
</html>
```